Business Card for Professional Photographer

I'm looking for an eye catching modern clean design that compliments my logo/ website fonts & colours.
I specialise in architecture, corporate & commercial photography so I'm marketing to professional clients rather than portrait / wedding clients.

I would prefer to not have a solid black design.

My logo brand guide is as follows :

Main front font. : Reislust
Main font colour : #fff
Slogan front font : Ubuntu Bold
Monogram front font : Venti Medium
Container colour : #fff

I need print ready files in pdf .png & .eps formats.

Included in the files below are some screen grabs as reference to font & colours etc.

```html
<!DOCTYPE html>
<html lang="en">
<head>
<meta charset="utf-8">
<title>Clear Angle – Business Card</title>
<link rel="stylesheet" href="https://fonts.googleapis.com/css2?family=Lato:wght@400;700&display=swap">
<style>
  :root {
    --page-bg: #bdbdbd;
    --card-bg: #151419;
    --gold-dark: #b68a32;
    --gold-mid: #e2c173;
    --gold-light: #f8ec9f;
    --text-light: #e9e9e9;
    --white: #ffffff;
  }
  * { margin: 0; padding: 0; box-sizing: border-box; }
  html, body {
    width: 1200px; height: 802px; overflow: hidden;
    background: var(--page-bg);
  }
  .canvas { position: relative; width: 1200px; height: 802px; }

  .card {
    position: absolute; top: 274px;
    width: 443px; height: 265px;
    background: var(--card-bg);
    box-shadow: 2px 3px 6px rgba(0,0,0,0.35);
    overflow: hidden;
  }
  .card--front { left: 136px; }
  .card--back  { left: 624px; }

  .gold-band {
    position: absolute; top: 0; right: 0;
    width: 50px; height: 100%;
    background: linear-gradient(90deg, var(--gold-dark) 0%, var(--gold-mid) 45%, var(--gold-light) 100%);
  }

  .identity { position: absolute; left: 29px; top: 61px; font-family: "Lato", sans-serif; }
  .identity__name {
    font-weight: 700; font-size: 16px; letter-spacing: 0.2px;
    color: var(--gold-mid);
    line-height: 1.1;
  }
  .identity__role { font-size: 12.5px; color: var(--text-light); line-height: 1.2; }

  .contacts { position: absolute; left: 29px; top: 110px; list-style: none; font-family: "Lato", sans-serif; }
  .contacts li {
    display: flex; align-items: center; gap: 5px;
    font-size: 12.5px; color: var(--text-light); line-height: 16px;
  }
  .contacts svg { width: 10px; height: 10px; flex: none; }

  .address {
    position: absolute; left: 29px; top: 170px;
    font-family: "Lato", sans-serif; font-style: normal;
    font-size: 12.5px; line-height: 16px; color: var(--text-light);
  }

  .wordmark {
    position: absolute; inset: 0;
    display: flex; flex-direction: column;
    align-items: center; justify-content: center;
    font-family: "Lato", sans-serif; text-align: center;
  }
  .wordmark__name {
    font-weight: 400; font-size: 28px; letter-spacing: 0.5px;
    color: var(--white); line-height: 1;
  }
  .wordmark__tagline {
    margin-top: 10px;
    font-weight: 400; font-size: 11px; letter-spacing: 0.3px;
    color: var(--text-light);
  }
</style>
</head>
<body>
<main class="canvas">

  <section class="card card--front">
    <div class="identity">
      <p class="identity__name">DANIEL HARTLEY</p>
      <p class="identity__role">Managing Director</p>
    </div>

    <ul class="contacts">
      <li>
        <svg viewBox="0 0 10 10" aria-hidden="true"><path d="M1 3.5 Q5 0.5 9 3.5 L8 4.8 L6.6 4 L6.6 3.2 Q5 2.6 3.4 3.2 L3.4 4 L2 4.8 Z M2.3 5.4 H7.7 L8.5 9 H1.5 Z" fill="var(--gold-mid)"/></svg>
        044-987 654 321
      </li>
      <li>
        <svg viewBox="0 0 10 10" aria-hidden="true"><rect x="0.5" y="2" width="9" height="6.5" fill="var(--gold-mid)"/><path d="M0.8 2.4 L5 5.8 L9.2 2.4" fill="none" stroke="var(--card-bg)" stroke-width="0.9"/></svg>
        hello@clearangle.com
      </li>
      <li>
        <svg viewBox="0 0 10 10" aria-hidden="true"><circle cx="5" cy="5" r="4.5" fill="var(--gold-mid)"/><path d="M3 2.5 Q4.5 3.5 3.6 5 Q5.5 5.6 5 7.6 M6.3 1.6 Q6 3 7.6 3.8" fill="none" stroke="var(--card-bg)" stroke-width="0.9"/></svg>
        www.clearangle.com
      </li>
    </ul>

    <address class="address">
      87, Harbour Lane,<br>
      30214,Country Name
    </address>

    <div class="gold-band"></div>
  </section>

  <section class="card card--back">
    <div class="wordmark">
      <p class="wordmark__name">Clear Angle</p>
      <p class="wordmark__tagline">Buildings, business and brand photography</p>
    </div>
  </section>

</main>
</body>
</html>
```